Homemaking training schools needs a Business Card design

Designer, Hello!

No special requirements, good-looking enough.
--------------------------------------------------------------------------

Name: Marcus Dole
Chairman
Tel: 0574-71948263
Mobile: 13857420916
Email: kelvora@mailnest.example
Web: www.prt2019.example
Add: No.258, LanpingJie, BeiyuanQu, Ningbo, Zhejiang

LOGO
Ningbo PRT Homemaking Training School

Target Market(s)

pregnant women, mothers, infants, the elderly and families, including cleaning, cooking, nursing training.

Industry/Entity Type

Business

Contact Information for Business Card

Name: Marcus Dole
Chairman
Tel: 0574-71948263
Mobile: 13857420916
Email: kelvora@mailnest.example
Web: www.prt2019.example

LOGO

Font styles to use
Serif
Sans Serif
Decorative

Requirements
Nice to have
• Feels: clean, specifications, safety, comfort, warmth and happiness.

```html
<!DOCTYPE html>
<html lang="en">
<head>
<meta charset="utf-8">
<title>PRT Homemaking Business Card</title>
<link rel="stylesheet" href="https://fonts.googleapis.com/css2?family=Arimo:wght@400;700&display=swap">
<style>
  :root {
    --stage: #2b2b2d;
    --magenta: #e8058a;
    --magenta-deep: #d10079;
    --blue: #1b6fb8;
    --ink: #3a3a3a;
    --paper: #f7f7f7;
    --paper-shade: #e9e9e9;
    --tint: #f6c9df;
    --white: #ffffff;
  }
  * { box-sizing: border-box; margin: 0; padding: 0; }
  html, body { width: 1200px; height: 997px; overflow: hidden; }
  body {
    background: var(--stage);
    font-family: "Arimo", Arial, sans-serif;
    position: relative;
  }
  .card {
    position: absolute;
    left: 250px;
    width: 700px;
    height: 400px;
    border-radius: 26px;
    overflow: hidden;
  }
  .card--front {
    top: 60px;
    background: linear-gradient(160deg, var(--magenta) 0%, var(--magenta-deep) 100%);
  }
  .card--back {
    top: 537px;
    background: linear-gradient(180deg, var(--paper) 0%, var(--paper-shade) 100%);
  }

  /* name block */
  .brand { position: absolute; text-align: center; }
  .brand__name {
    font-weight: 700;
    font-size: 40px;
    color: var(--blue);
    line-height: 1.1;
  }
  .brand__tag {
    margin-top: 8px;
    font-size: 14px;
    letter-spacing: 3px;
    text-transform: uppercase;
    color: var(--ink);
  }
  .card--front .brand { left: 0; right: 0; top: 160px; }
  .card--front .brand__tag { color: var(--white); }
  .card--back .brand { left: 20px; width: 390px; top: 150px; }
  .card--back .brand__name { font-size: 34px; }
  .card--back .brand__tag { font-size: 12.5px; }

  .web {
    position: absolute;
    left: 40px;
    bottom: 48px;
    font-weight: 700;
    font-size: 20px;
    letter-spacing: 2.5px;
    color: var(--blue);
  }
  .web__domain { color: var(--magenta); }

  .panel { position: absolute; inset: 0; }

  .person {
    position: absolute;
    left: 468px;
    top: 44px;
    color: var(--white);
  }
  .person__name { font-size: 24px; letter-spacing: 0.3px; }
  .person__title { font-size: 13px; margin-top: 4px; }

  .contacts {
    position: absolute;
    left: 458px;
    top: 188px;
    list-style: none;
    color: var(--white);
    font-size: 14.5px;
    letter-spacing: 0.3px;
    white-space: nowrap;
  }
  .contacts__item {
    display: flex;
    align-items: flex-start;
    gap: 12px;
    margin-bottom: 14px;
    line-height: 1.25;
  }
  .contacts__icon {
    flex: 0 0 22px;
    width: 22px; height: 22px;
    border-radius: 3px;
    background: var(--tint);
    display: flex; align-items: center; justify-content: center;
  }
  .contacts__icon svg { width: 14px; height: 14px; fill: var(--magenta); }
  .contacts__text { padding-top: 2px; }
</style>
</head>
<body>

<section class="card card--front" aria-label="Card front">
  <div class="brand">
    <p class="brand__name">PRT Homemaking</p>
    <p class="brand__tag">Training School · Ningbo</p>
  </div>
</section>

<section class="card card--back" aria-label="Card back">
  <svg class="panel" viewBox="0 0 700 400" width="700" height="400" aria-hidden="true">
    <path d="M424 0 H700 V400 H424 V84 L406 66 L424 48 Z" fill="var(--magenta)"/>
    <path d="M434 0 H700 V400 H434 V84 L416 66 L434 48 Z" fill="var(--blue)"/>
  </svg>

  <div class="brand">
    <p class="brand__name">PRT Homemaking</p>
    <p class="brand__tag">Training School · Ningbo</p>
  </div>

  <p class="web">www.<span class="web__domain">prt2019</span>.example</p>

  <div class="person">
    <p class="person__name">Marcus Dole</p>
    <p class="person__title">Chairman</p>
  </div>

  <ul class="contacts">
    <li class="contacts__item">
      <span class="contacts__icon"><svg viewBox="0 0 16 16"><path d="M2 5c0-2 2-3 6-3s6 1 6 3v1h-3V5H5v1H2zM4 7h8l2 6H2z"/></svg></span>
      <span class="contacts__text">0574-71948263</span>
    </li>
    <li class="contacts__item">
      <span class="contacts__icon"><svg viewBox="0 0 16 16"><path d="M4 1h8v4H4zM1 6h14v6h-3v3H4v-3H1zM5 10v4h6v-4z"/></svg></span>
      <span class="contacts__text">13857420916</span>
    </li>
    <li class="contacts__item">
      <span class="contacts__icon"><svg viewBox="0 0 16 16"><path d="M1 3h14v10H1zM2 4.5v.6l6 4 6-4v-.6z"/></svg></span>
      <span class="contacts__text">kelvora@mailnest.example</span>
    </li>
    <li class="contacts__item">
      <span class="contacts__icon"><svg viewBox="0 0 16 16"><path d="M8 1l7 6h-2v8H9.5v-5h-3v5H3V7H1z"/></svg></span>
      <span class="contacts__text">No.258, LanpingJie<br>BeiyuanQu, Ningbo, Zhejiang</span>
    </li>
  </ul>
</section>

</body>
</html>
```